Renny Oskow - Free Personalised Health Consultation - "One size does not fit all"

This flyer will be left on tables/seats at speaking events and seminars and used to attain leads.

Top half will have "SMS me for a FREE Personalised Health Consultation" and my picture (see www.rennyoskow-demo.com and pick most engaging photo) and underneath my contact details. It must have lines with "Notes:" halfway down so people can take notes at the seminar and lines on the back with my contact details again and "Notes: with lines.

I am having a business card also being designed by Artvane for same and would like the flyer and business card to carry a similar feel/look for consistency.

Below is the brief for the business card being designed:
Business Card for www.rennyoskow-demo.com site. It is a trust site and I use it for 1:1 relatable connections. It is the one I use for building intimate 1:1 trust building and Exec Coaching Services and programs for high wealth individuals and corporates. I also have a commercial programmatic site of my personal health products and services and programs for main stream one to many. www.steadyforwardliving-demo.com that can also provoke thought for the www.rennyoskow-demo.com business card. (mind you will get a separate business card for that site, but want to provide context). It has a logo which you may want to draw from in designing the rennyoskow business card which is personal and is about building my brand. There is also a rennyoskow personal PX page and rennyoskow business PX page. I am a Certified Talent Compass 3.1 Coach with Norvik and you can get a corporate brief of me on there to give you more context https://www.norvikcoachhub-demo.com/coach/en-us/directory?search=renny

Target Market(s)

Exec, IT, Health conscious. Corporates wanting to run Health and Wellness programs. Those wanting to go from good to great. Millennials to Middleaged.

Industry/Entity Type

Health And Wellness

Font styles to use
Sans Serif
Other font styles liked:
• Arial and Calibri ok too

Colors

Designer to choose colors to be used in the design.

Requirements
Must have
• Picture of me - use best from www.rennyoskow-demo.com or can send one you choose.
• Contact details like my buisness card being designed by you guys in separate project.
• Name: Renny Oskow
• email: renny@rennyoskow-demo.,com
• Phone: Australia +61 400 000 137 Singapore: +65 9000 2468
Nice to have
• Open to ideas

```html
<!DOCTYPE html>
<html lang="en">
<head>
<meta charset="utf-8">
<title>Renny Oskow – Free Personalised Health Consultation Flyer</title>
<link href="https://fonts.googleapis.com/css2?family=Fjalla+One&family=Roboto:wght@400;500;700&display=swap" rel="stylesheet">
<style>
  :root {
    --backdrop: #e9e9e9;
    --paper: #ffffff;
    --ink: #1f1f1f;
    --footer-band: #2a2a2a;
    --footer-text: #f2f2f2;
    --rule: #8a8a8a;
    --panel: rgba(70, 70, 70, 0.82);
    --photo-light: #d9d9d9;
    --photo-mid: #9a9a9a;
    --photo-dark: #3c3c3c;
  }
  * { margin: 0; padding: 0; box-sizing: border-box; }
  html, body { width: 1200px; height: 903px; overflow: hidden; }
  body { background: var(--backdrop); font-family: 'Roboto', Arial, sans-serif; color: var(--ink); position: relative; }

  .flyer {
    position: absolute; top: 80px; width: 526px; height: 744px;
    background: var(--paper); box-shadow: 0 2px 8px rgba(0,0,0,0.18);
  }
  .flyer--front { left: 58px; }
  .flyer--back { left: 617px; }

  .hero-photo {
    position: absolute; left: 0; top: 0; width: 526px; height: 428px;
    background: linear-gradient(100deg, var(--photo-light) 0%, var(--photo-mid) 45%, var(--photo-dark) 62%, var(--photo-mid) 80%, var(--photo-light) 100%);
  }
  .offer-panel {
    position: absolute; left: 24px; top: 88px; width: 264px; height: 267px;
    background: var(--panel); color: #fff; text-align: right;
    padding: 20px 22px 0 0;
  }
  .offer-lead { font-family: 'Fjalla One', 'Arial Narrow', sans-serif; font-size: 38px; line-height: 1; letter-spacing: -0.5px; }
  .offer-free { font-family: 'Fjalla One', 'Arial Narrow', sans-serif; font-size: 118px; line-height: 0.98; letter-spacing: 1px; margin-top: 2px; }
  .offer-service { font-weight: 700; font-size: 25px; line-height: 1.1; margin-top: 2px; }
  .offer-detail { font-weight: 500; font-size: 17px; line-height: 1.2; margin-top: 4px; }
  .offer-signature { font-size: 15px; margin-top: 14px; }

  .notes-heading { position: absolute; left: 24px; font-size: 20px; font-weight: 400; letter-spacing: 0.3px; }
  .flyer--front .notes-heading { top: 442px; }
  .flyer--back .notes-heading { top: 24px; }

  .note-lines { position: absolute; left: 24px; width: 478px; list-style: none; }
  .note-lines li { height: 40.5px; border-bottom: 1px dotted var(--rule); }
  .flyer--front .note-lines { top: 455px; }
  .flyer--back .note-lines { top: 36px; }

  .contact-band {
    position: absolute; left: 0; top: 692px; width: 526px; height: 36px;
    background: var(--footer-band); color: var(--footer-text);
    display: flex; align-items: center; justify-content: space-between;
    padding: 0 26px 0 28px; font-size: 11px; list-style: none;
  }
  .contact-band li { display: flex; align-items: center; gap: 6px; white-space: nowrap; }
  .contact-band svg { width: 12px; height: 12px; fill: var(--footer-text); }
</style>
</head>
<body>

<article class="flyer flyer--front">
  <div class="hero-photo" role="img" aria-label="Black and white photo of Renny Oskow in a dark suit, smiling and leaning on a bicycle on a shaded veranda beside a white bench"></div>
  <div class="offer-panel">
    <p class="offer-lead">SMS me for a</p>
    <p class="offer-free">FREE</p>
    <p class="offer-service">PERSONALISED</p>
    <p class="offer-detail">HEALTH CONSULTATION</p>
    <p class="offer-signature">- Renny Oskow</p>
  </div>
  <h2 class="notes-heading">NOTES</h2>
  <ul class="note-lines"><li></li><li></li><li></li><li></li><li></li></ul>
  <ul class="contact-band">
    <li><svg viewBox="0 0 24 24"><path d="M6.6 10.8c1.4 2.8 3.8 5.1 6.6 6.6l2.2-2.2c.3-.3.7-.4 1-.2 1.1.4 2.3.6 3.6.6.6 0 1 .4 1 1V20c0 .6-.4 1-1 1C10.6 21 3 13.4 3 4c0-.6.4-1 1-1h3.5c.6 0 1 .4 1 1 0 1.2.2 2.4.6 3.6.1.3 0 .7-.2 1z"/></svg>Australia +61 400 000 137</li>
    <li><svg viewBox="0 0 24 24"><path d="M6.6 10.8c1.4 2.8 3.8 5.1 6.6 6.6l2.2-2.2c.3-.3.7-.4 1-.2 1.1.4 2.3.6 3.6.6.6 0 1 .4 1 1V20c0 .6-.4 1-1 1C10.6 21 3 13.4 3 4c0-.6.4-1 1-1h3.5c.6 0 1 .4 1 1 0 1.2.2 2.4.6 3.6.1.3 0 .7-.2 1z"/></svg>Singapore: +65 9000 2468</li>
    <li><svg viewBox="0 0 24 24"><path d="M3 5h18v14H3z M3 5l9 7 9-7" fill="none" stroke="#f2f2f2" stroke-width="2"/></svg>renny@rennyoskow-demo.com</li>
  </ul>
</article>

<article class="flyer flyer--back">
  <h2 class="notes-heading">NOTES</h2>
  <ul class="note-lines">
    <li></li><li></li><li></li><li></li><li></li><li></li><li></li><li></li>
    <li></li><li></li><li></li><li></li><li></li><li></li><li></li>
  </ul>
  <ul class="contact-band">
    <li><svg viewBox="0 0 24 24"><path d="M6.6 10.8c1.4 2.8 3.8 5.1 6.6 6.6l2.2-2.2c.3-.3.7-.4 1-.2 1.1.4 2.3.6 3.6.6.6 0 1 .4 1 1V20c0 .6-.4 1-1 1C10.6 21 3 13.4 3 4c0-.6.4-1 1-1h3.5c.6 0 1 .4 1 1 0 1.2.2 2.4.6 3.6.1.3 0 .7-.2 1z"/></svg>Australia +61 400 000 137</li>
    <li><svg viewBox="0 0 24 24"><path d="M6.6 10.8c1.4 2.8 3.8 5.1 6.6 6.6l2.2-2.2c.3-.3.7-.4 1-.2 1.1.4 2.3.6 3.6.6.6 0 1 .4 1 1V20c0 .6-.4 1-1 1C10.6 21 3 13.4 3 4c0-.6.4-1 1-1h3.5c.6 0 1 .4 1 1 0 1.2.2 2.4.6 3.6.1.3 0 .7-.2 1z"/></svg>Singapore: +65 9000 2468</li>
    <li><svg viewBox="0 0 24 24"><path d="M3 5h18v14H3z M3 5l9 7 9-7" fill="none" stroke="#f2f2f2" stroke-width="2"/></svg>renny@rennyoskow-demo.com</li>
  </ul>
</article>

</body>
</html>
```